Stationary design for boutique production house

We need a stationary design for our production house, 'Lorno Productions' based in Singapore. We produce microfilms as well as podcasts, talkshows and events. Our logo is a stylized icon of our director, who is also the executive producer and host of our programs, Lorno. Our main company colors are Red, Black and white. We would like a clean, minimalist design incorporating our existing company logo that conveys a sense of urbanism and elegance.

Logo and font files are attached. f

Target Market(s)

We focus on lifestyle media rather than entertainment.

Industry/Entity Type

Boutique

Font styles to use
Serif
Sans Serif

Colors
ec1f27
ffffff
000000

Requirements
Must have
• Our company logo and at least one of our company colors.
Nice to have
• Our address and contact information.
Should not have
• Changes made to the company logo (using only certain parts of it is fine though)

```html
<!DOCTYPE html>
<html lang="en">
<head>
<meta charset="utf-8">
<title>Lorno Productions – Business Card</title>
<link href="https://fonts.googleapis.com/css2?family=Jost:wght@400;500&display=swap" rel="stylesheet">
<style>
  :root {
    --red: #ec1f27;
    --black: #000000;
    --ink: #2b2b2b;
    --grey-text: #444444;
    --rule: #8a8a8a;
    --white: #ffffff;
    --paper: #fbfbfb;
    --backdrop: #e6e6e6;
  }
  * { margin: 0; padding: 0; box-sizing: border-box; }
  html, body {
    width: 1200px; height: 750px; overflow: hidden;
    background: var(--backdrop);
    font-family: "Jost", "Futura", sans-serif;
  }
  .sheet {
    position: relative; width: 1200px; height: 750px;
    display: flex; justify-content: center; align-items: center; gap: 20px;
  }
  .card {
    position: relative; width: 540px; height: 307px; overflow: hidden;
  }

  /* Front */
  .card-front { background: var(--paper); color: var(--ink); }
  .brand {
    position: absolute; right: 37px; top: 46px;
    display: flex; align-items: center; gap: 10px;
  }
  .brand-dot { width: 14px; height: 14px; border-radius: 50%; background: var(--red); }
  .brand-name {
    font-size: 19px; font-weight: 500; line-height: 1.1;
    color: var(--black); text-transform: uppercase; letter-spacing: 1px; text-align: right;
  }
  .person-name {
    position: absolute; left: 30px; top: 150px;
    font-size: 21px; font-weight: 400; color: var(--red); text-transform: uppercase;
  }
  .person-title {
    position: absolute; left: 30px; top: 176px; right: 36px;
    display: flex; align-items: center; gap: 5px;
    font-size: 15px; text-transform: uppercase; color: var(--ink);
  }
  .person-title::after { content: ""; flex: 1; height: 1px; background: var(--rule); }
  .contact-list {
    position: absolute; left: 30px; top: 204px; list-style: none;
    font-size: 14px; color: var(--grey-text);
  }
  .contact-list li { display: flex; align-items: center; gap: 9px; height: 20.5px; }
  .contact-list li.email { font-size: 13px; }
  .contact-icon { width: 13px; height: 13px; flex: none; }
  .address {
    position: absolute; right: 37px; top: 222px; text-align: right;
    font-size: 14px; line-height: 19.5px; color: var(--grey-text); font-style: normal;
  }
  .footer-band {
    position: absolute; left: 0; bottom: 12px; width: 100%; height: 16px;
    display: flex;
  }
  .footer-band .band-red {
    flex: 1; background: var(--red); color: var(--white);
    font-size: 12px; letter-spacing: 2.2px; line-height: 16px; padding-left: 29px;
  }
  .footer-band .band-black { width: 48px; background: var(--black); position: relative; }
  .band-marker {
    position: absolute; left: -6px; top: 3px; width: 10px; height: 13px;
    border-radius: 5px 5px 0 0; background: var(--white);
  }

  /* Back */
  .card-back { background: var(--red); color: var(--white); }
  .back-brand {
    position: absolute; left: 0; right: 0; top: 112px;
    display: flex; justify-content: center; align-items: center; gap: 14px;
  }
  .back-brand .brand-dot { width: 22px; height: 22px; background: var(--white); }
  .back-brand .brand-name { font-size: 34px; color: var(--white); letter-spacing: 3px; text-align: left; }
  .back-web {
    position: absolute; left: 0; right: 0; top: 262px; text-align: center;
    font-size: 13px; letter-spacing: 7.5px; color: var(--white);
  }
</style>
</head>
<body>
<main class="sheet">
  <section class="card card-front">
    <div class="brand">
      <span class="brand-dot"></span>
      <span class="brand-name">Lorno<br>Productions</span>
    </div>

    <h1 class="person-name">Mara Quinlan</h1>
    <p class="person-title">CEO/Founder</p>

    <ul class="contact-list">
      <li>
        <svg class="contact-icon" viewBox="0 0 24 24"><path fill="#ec1f27" d="M6.6 10.8a15.1 15.1 0 0 0 6.6 6.6l2.2-2.2c.3-.3.7-.4 1-.2 1.1.4 2.3.6 3.6.6.6 0 1 .4 1 1V20c0 .6-.4 1-1 1A17 17 0 0 1 3 4c0-.6.4-1 1-1h3.5c.6 0 1 .4 1 1 0 1.3.2 2.5.6 3.6.1.3 0 .7-.2 1z"/></svg>
        6512 4830
      </li>
      <li>
        <svg class="contact-icon" viewBox="0 0 24 24"><rect x="5" y="1.5" width="14" height="21" rx="2" fill="#ec1f27"/><rect x="7.5" y="4.5" width="9" height="13" fill="#fbfbfb"/><circle cx="12" cy="20" r="1.2" fill="#fbfbfb"/></svg>
        9127 5564
      </li>
      <li class="email">
        <svg class="contact-icon" viewBox="0 0 24 24"><rect x="1.5" y="5" width="21" height="14" fill="#ec1f27"/><path d="M2 6l10 7 10-7" fill="none" stroke="#fbfbfb" stroke-width="1.6"/></svg>
        mara@lornostudio.sg
      </li>
    </ul>

    <address class="address">48 Keong Saik Road<br>Singapore 089154</address>

    <div class="footer-band">
      <div class="band-red">www.lornostudio.sg</div>
      <div class="band-black"><span class="band-marker"></span></div>
    </div>
  </section>

  <section class="card card-back">
    <div class="back-brand">
      <span class="brand-dot"></span>
      <span class="brand-name">Lorno<br>Productions</span>
    </div>
    <p class="back-web">www.lornostudio.sg</p>
  </section>
</main>
</body>
</html>
```